Catering Company Website Design

We are working with a bbq catering company in California called Ember Plank Catering.
Some sites to use for content/competitors and inspiration:
https://19parsnips.com
https://mbetrovandel.com
https://ridgefeastco.com
https://tinforkdenvale.com (client's favorite)
https://www.marvenasmokehut.com (client's favorite)
https://www.theopenkettlekitchen.com
Thank you for taking the time to consider designing a website for us. We are web developers based in Stockton, CA, USA. Most of our projects go through the same process. Understanding this process may help you win a project with us. We custom-code all of our websites in-house. We don’t have any requirements as to what tools you use for your design, but we prefer Figma files. For any design that we label as four-stars, we send it to the client for review. The client picks the final design they want us to use. Once we complete this process, we will continue to show additional clients all the four-star sites and purchase them later. Your designs will have multiple chances to sell. For better chances of success, we ask that you follow these guidelines.
IMAGES:
If you use any images or icons in the design, we ask that you have a link to the asset so we can purchase the image/icon. Most of the designs we submit do not have the customer’s images on them unless they have some great images. Be creative; show us the feeling you are trying to portray with your image choices. Use any royalty-free site you choose. We subscribe to Zelvio and mainly use their images, but we can purchase images outside of Zelvio.
PLEASE NOTE: we will not submit designs to clients with watermarks on the images.
FONTS:
We ask that you identify the fonts used in the design. This can be done in a message if you want. We typically use Google Fonts and Zelvio Fonts.
CONTENT:
We're always open to different content and ideas. We often submit designs with stock images so the client can see our vision. We typically take pictures after the website launch to use their images with our vision. Lorem Ipsum is fine for paragraphs, but we ask that you write the headers in correct English. We want to be able to show the vision and identify the sections of the website.
INSPIRATION:
We typically add a couple of links in the brief of websites we like to help you get started in your design.
REVISIONS:
We do not often ask for revisions of the designs unless we see something in the design that may not appeal to the client. If there are slight changes that we want to make, we do that in the development process.
FEEDBACK:
We rarely give feedback on designs during the design process. We are working on many website projects and do not have the time to provide feedback. We usually respond if your request is well thought out and asks specific questions, but a note asking “feedback, please” usually goes unanswered

```html
<!DOCTYPE html>
<html lang="en">
<head>
<meta charset="utf-8">
<title>Ember Plank Catering</title>
<link href="https://fonts.googleapis.com/css2?family=Titillium+Web:wght@400;600;700&family=Open+Sans:wght@400;600&display=swap" rel="stylesheet">
<style>
:root{
  --red:#c8161d;
  --red-dark:#a01015;
  --ink:#1b1b1b;
  --text:#333333;
  --muted:#6a6a6a;
  --white:#ffffff;
  --band:#e8e8e8;
  --black:#0c0c0c;
}
*{box-sizing:border-box;margin:0;padding:0}
html,body{width:1200px;height:4472px;overflow:hidden}
body{position:relative;background:var(--white);font-family:"Open Sans",Arial,sans-serif;color:var(--text)}
.abs{position:absolute}
.heading{font-family:"Titillium Web",Arial,sans-serif;font-weight:600;color:var(--ink);text-transform:uppercase;line-height:1.1}
.heading em{font-style:normal;color:var(--red);font-weight:700}
.btn{display:inline-flex;align-items:center;justify-content:center;background:var(--red);color:var(--white);font-family:"Titillium Web",Arial,sans-serif;font-weight:700;font-size:15px;text-transform:uppercase;border-radius:22px;height:44px;padding:0 28px;letter-spacing:.3px;white-space:nowrap}
.mark{width:26px;height:26px;border-radius:50%;background:var(--red);flex:none}
.body-copy{font-size:15px;line-height:1.6}

/* hero */
.hero{left:0;top:0;width:1200px;height:528px;background:linear-gradient(100deg,#1a1514 0%,#2a211d 45%,#4a2a1c 70%,#6d2e18 100%)}
.hero-photo{left:560px;top:0;width:640px;height:528px;background:radial-gradient(ellipse at 60% 40%,#8a3a1c 0%,#5a2a1a 40%,rgba(40,28,24,0) 75%)}
.brand{left:112px;top:36px;width:160px;font-family:"Titillium Web",Arial,sans-serif;font-weight:700;font-size:16px;line-height:1.15;color:var(--white);text-transform:uppercase;display:flex;align-items:center;gap:10px}
.nav{left:300px;top:48px;display:flex;gap:40px;font-family:"Titillium Web",Arial,sans-serif;font-weight:600;font-size:16px;color:var(--white);text-transform:uppercase}
.nav .active{color:var(--red);border-bottom:2px solid var(--red);padding-bottom:4px}
.order{left:944px;top:40px;height:44px;border-radius:22px;font-size:15px}
.hero-kicker{left:112px;top:244px;font-family:"Titillium Web",Arial,sans-serif;font-weight:600;font-size:36px;line-height:40px;color:var(--red);text-transform:uppercase}
.hero-title{left:112px;top:284px;font-family:"Titillium Web",Arial,sans-serif;font-weight:700;font-size:44px;line-height:48px;color:var(--white);text-transform:uppercase}
.hero-copy{left:112px;top:338px;width:460px;color:#eee;font-size:14px;line-height:1.5}
.hero-btn{left:112px;top:394px}
.arrow{width:40px;height:40px;border-radius:50%;top:454px;display:flex;align-items:center;justify-content:center}
.arrow.prev{left:116px;background:var(--white)}
.arrow.next{left:164px;background:#555}

/* services */
.section-mark{left:587px}
.services-heading{left:0;width:1200px;top:706px;text-align:center;font-size:42px}
.card{width:592px;height:384px;overflow:hidden}
.card .overlay{position:absolute;inset:0;background:linear-gradient(180deg,rgba(0,0,0,.15),rgba(0,0,0,.6))}
.card h3{position:absolute;left:112px;top:196px;font-family:"Titillium Web",Arial,sans-serif;font-weight:600;font-size:30px;color:var(--white);text-transform:uppercase}
.card p{position:absolute;left:112px;top:240px;width:380px;color:#eee;font-size:13px;line-height:1.5}
.card .btn{position:absolute;left:112px;top:292px;height:40px;font-size:14px}

/* story */
.story-frame{left:88px;top:1664px;width:260px;height:400px;border:3px solid var(--red)}
.story-photo{left:108px;top:1684px;width:492px;height:508px;background:linear-gradient(160deg,#b98a66 0%,#6d4a34 50%,#2c1d16 100%)}
.story-inset{left:328px;top:1952px;width:272px;height:240px;background:linear-gradient(150deg,#ff9a3c 0%,#c6421a 45%,#3a1a10 100%);border:6px solid var(--white)}
.story-text{left:660px;top:1700px;width:436px}
.story-text .heading{font-size:40px;margin:18px 0 20px}
.story-text .body-copy{margin-bottom:16px}

/* experience */
.band{left:0;top:2312px;width:1200px;height:488px;background:var(--band)}
.experience-heading{left:0;width:1200px;top:2424px;text-align:center;font-size:42px}
.video{left:112px;top:2528px;width:976px;height:480px;border-radius:28px;background:linear-gradient(180deg,#f0c48a 0%,#e28d4e 40%,#7a4a33 75%,#2e1f19 100%)}
.play{left:564px;top:2732px;width:72px;height:72px;border-radius:50%;background:var(--red);display:flex;align-items:center;justify-content:center}

/* feature rows */
.feature-photo{border-radius:22px}
.food-photo{left:108px;top:3084px;width:504px;height:372px;background:linear-gradient(135deg,#7a3d28 0%,#4a2418 55%,#1f120d 100%)}
.venue-photo{left:580px;top:3612px;width:508px;height:376px;background:linear-gradient(135deg,#5a2a1e 0%,#3a1a12 55%,#140a08 100%)}
.feature-card{background:var(--white);box-shadow:0 8px 30px rgba(0,0,0,.12);padding:28px 40px}
.food-card{left:560px;top:3192px;width:528px;height:336px}
.venue-card{left:104px;top:3572px;width:528px;height:316px}
.feature-card .label{font-size:34px;font-weight:400}
.feature-card .title{font-family:"Titillium Web",Arial,sans-serif;font-weight:600;font-size:34px;color:var(--red);text-transform:uppercase;line-height:1.15;margin:12px 0 14px}
.feature-card .body-copy{font-size:14px;margin-bottom:16px}

/* footer */
.footer{left:0;top:4072px;width:1200px;height:400px;background:var(--black);color:var(--white)}
.footer-brand{left:112px;top:160px;width:300px;font-family:"Titillium Web",Arial,sans-serif;font-weight:700;font-size:32px;text-transform:uppercase;line-height:1.1}
.footer-col{top:88px}
.footer-col h4{font-family:"Titillium Web",Arial,sans-serif;font-weight:700;font-size:24px;text-transform:uppercase;border-left:4px solid var(--red);padding-left:10px;margin-bottom:20px}
.footer-col li{list-style:none;font-size:16px;text-transform:uppercase;line-height:42px;padding-left:14px}
.copyright{left:672px;top:336px;font-size:14px;color:#ddd}
</style>
</head>
<body>

<header class="hero abs">
  <div class="hero-photo abs" role="img" aria-label="Sausages and peppers sizzling on a flaming grill"></div>
  <div class="brand abs"><span class="mark"></span><span>Ember Plank<br>Catering</span></div>
  <nav class="nav abs">
    <span class="active">Home</span><span>About</span><span>Services</span><span>Events</span><span>Venues</span><span>Careers</span>
  </nav>
  <span class="btn order abs">Order Online</span>
  <div class="hero-kicker abs">California</div>
  <h1 class="hero-title abs">Ember Plank Catering</h1>
  <p class="hero-copy abs">Lorem ipsum dolor sit amet, consectetur adipiscing elit, sed do eiusmod tempor incididunt ut labore et dolore magna aliqua.</p>
  <span class="btn hero-btn abs">View Specials</span>
  <span class="arrow prev abs"><svg width="16" height="16" viewBox="0 0 16 16"><path d="M10 3 5 8l5 5" fill="none" stroke="#222" stroke-width="2"/></svg></span>
  <span class="arrow next abs"><svg width="16" height="16" viewBox="0 0 16 16"><path d="M6 3l5 5-5 5" fill="none" stroke="#fff" stroke-width="2"/></svg></span>
</header>

<span class="mark section-mark abs" style="top:640px"></span>
<h2 class="heading services-heading abs">Great Food &amp; A <em>Whole Lot More</em></h2>

<article class="card abs" style="left:0;top:788px;background:linear-gradient(135deg,#6b5446,#2e241e)" role="img" aria-label="Chefs preparing plated food at a catered event">
  <div class="overlay"></div>
  <h3>Gourmet Catering</h3>
  <p>Lorem ipsum dolor sit amet, consectetur adipiscing elit, sed do eiusmod tempor incididunt ut labore.</p>
  <span class="btn">View More</span>
</article>
<article class="card abs" style="left:608px;top:788px;background:linear-gradient(135deg,#b8b8b8,#4a4a4a)" role="img" aria-label="Uniformed catering staff standing together">
  <div class="overlay"></div>
  <h3>Staffing</h3>
  <p>Lorem ipsum dolor sit amet, consectetur adipiscing elit, sed do eiusmod tempor incididunt ut labore.</p>
  <span class="btn">View More</span>
</article>
<article class="card abs" style="left:0;top:1180px;background:linear-gradient(135deg,#7a3a1c,#1f140f)" role="img" aria-label="Lit bar counter with bottles and glasses">
  <div class="overlay"></div>
  <h3>Bar Service</h3>
  <p>Lorem ipsum dolor sit amet, consectetur adipiscing elit, sed do eiusmod tempor incididunt ut labore.</p>
  <span class="btn">View More</span>
</article>
<article class="card abs" style="left:608px;top:1180px;background:linear-gradient(135deg,#3a4a8a,#10142e)" role="img" aria-label="Event stage with screen and lighting">
  <div class="overlay"></div>
  <h3>Event Production</h3>
  <p>Lorem ipsum dolor sit amet, consectetur adipiscing elit, sed do eiusmod tempor incididunt ut labore.</p>
  <span class="btn">View More</span>
</article>

<section>
  <div class="story-frame abs"></div>
  <div class="story-photo abs" role="img" aria-label="Guests serving food from an outdoor grill"></div>
  <div class="story-inset abs" role="img" aria-label="Sausages over open flames"></div>
  <div class="story-text abs">
    <span class="mark" style="display:block"></span>
    <h2 class="heading">Our <em>Story</em></h2>
    <p class="body-copy">Lorem ipsum dolor sit amet, consectetur adipiscing elit, sed do eiusmod tempor incididunt ut labore et dolore magna aliqua. Ut enim ad minim veniam, quis nostrud exercitation ullamco laboris nisi ut aliquip ex ea commodo consequat. Duis aute irure dolor in reprehenderit in voluptate velit esse cillum dolore eu fugiat nulla pariatur.</p>
    <p class="body-copy">Lorem ipsum dolor sit amet, consectetur adipiscing elit, sed do eiusmod tempor incididunt ut labore et dolore magna aliqua. Ut enim ad minim veniam.</p>
    <span class="btn">Read More</span>
  </div>
</section>

<div class="band abs"></div>
<span class="mark section-mark abs" style="top:2368px"></span>
<h2 class="heading experience-heading abs">Far More Than <em>Just Business</em></h2>
<div class="video abs" role="img" aria-label="Friends gathered around a beach barbecue at sunset"></div>
<span class="play abs"><svg width="28" height="28" viewBox="0 0 28 28"><path d="M9 5v18l15-9z" fill="#fff"/></svg></span>

<div class="feature-photo food-photo abs" role="img" aria-label="Sliced grilled steak with dipping sauces"></div>
<div class="feature-card food-card abs">
  <h3 class="heading label">Our Food</h3>
  <p class="title">Quality Food Made From Scratch</p>
  <p class="body-copy">Lorem ipsum dolor sit amet, consectetur adipiscing elit, sed do eiusmod tempor incididunt ut labore et dolore magna aliqua.</p>
  <span class="btn">Read More</span>
</div>

<div class="feature-card venue-card abs">
  <h3 class="heading label">Our Venues</h3>
  <p class="title">California Venue Authority</p>
  <p class="body-copy">Lorem ipsum dolor sit amet, consectetur adipiscing elit, sed do eiusmod tempor incididunt ut labore et dolore magna aliqua.</p>
  <span class="btn">Read More</span>
</div>
<div class="feature-photo venue-photo abs" role="img" aria-label="Sliced grilled steak on a dark board"></div>

<footer class="footer abs">
  <div class="footer-brand abs">Ember Plank Catering</div>
  <div class="footer-col abs" style="left:448px">
    <h4>Quick Links</h4>
    <ul><li>Home</li><li>About</li><li>Services</li><li>Events</li><li>Venues</li></ul>
  </div>
  <div class="footer-col abs" style="left:680px">
    <h4>Services</h4>
    <ul><li>Gourmet Catering</li><li>Bar Service</li><li>Staffing</li><li>Design &amp; Production</li></ul>
  </div>
  <div class="footer-col abs" style="left:928px">
    <h4>Events</h4>
    <ul><li>Weddings</li><li>Corporate</li><li>Social</li><li>Gallery</li></ul>
  </div>
  <p class="copyright abs">Copyright 2024 Ember Plank Catering All Rights Reserved</p>
</footer>

</body>
</html>
```